Website for 3d printing & other services

Hi, i'm after a website to sell my 3d printed automotive parts as well as sell my 3d printing services & other services.

There's a few things i need the website to have:

- Automatic 3d print quoting based on the file the client uploads to the website.
- Shop function where i can sell my custom automotive parts
- 3D printing technologies offered are SLA & FDM
- My business can offer 3d printing, 3d scanning, 3d cad design, cnc machining, steel fabrication, drafting services.

The color design is to suit my logo which is Black, orange & white.

Target Market(s)

3d printing, automotive, fabrication

Industry/Entity Type

General manufacturing & Custom automotive parts

Coding

Coded - Design and coding required

Number of Pages Required

5+ page

Requirements
Must have
• Automatic 3d print quoting. Shop for my printed parts.

```html
<!DOCTYPE html>
<html lang="en">
<head>
<meta charset="utf-8">
<title>Korvath Draft &amp; Design</title>
<link rel="stylesheet" href="https://fonts.googleapis.com/css2?family=Montserrat:wght@600;700;800&family=Roboto:wght@400;500;700&display=swap">
<style>
:root{
  --orange:#fc7a12;
  --orange-dark:#e86a06;
  --black:#161616;
  --charcoal:#232323;
  --cream:#fdf0e3;
  --text:#1b1b1b;
  --muted:#777;
  --line:#d9d9d9;
  --white:#fff;
}
*{box-sizing:border-box;margin:0;padding:0}
html,body{width:1200px;height:4345px;overflow:hidden}
body{position:relative;background:var(--white);font-family:Roboto,Arial,sans-serif;color:var(--text)}
.abs{position:absolute}
.btn{position:absolute;display:flex;align-items:center;justify-content:center;gap:8px;background:var(--orange);color:#fff;font:700 13px Roboto,Arial,sans-serif;text-transform:uppercase;border-radius:3px;white-space:nowrap}
.btn .dot{width:11px;height:11px;border-radius:50%;background:#fff;position:relative;flex:none}
.btn .dot::after{content:"";position:absolute;left:4px;top:3px;border:2.5px solid transparent;border-left:3.5px solid var(--orange);border-right:0}
.btn.ghost{background:#fff;color:var(--orange)}
.btn.ghost .dot{background:var(--orange)}
.btn.ghost .dot::after{border-left-color:#fff}
.sec-title{position:absolute;left:0;width:1200px;text-align:center;font:700 34px Montserrat,sans-serif;color:var(--black);text-transform:uppercase}
.sec-title::after{content:"";display:block;width:40px;height:2px;background:var(--orange);margin:14px auto 0}
.photo{position:absolute;overflow:hidden}

/* header */
.brand-block{left:0;top:0;width:300px;height:135px;background:var(--black);clip-path:polygon(0 0,255px 0,300px 135px,0 135px)}
.brand-name{left:74px;top:44px;width:190px;font:800 19px/1.2 Montserrat,sans-serif;color:var(--orange);text-transform:uppercase}
.socials{left:580px;top:29px;display:flex;gap:10px}
.socials span{width:32px;height:32px;border:1.5px solid var(--orange);border-radius:50%;display:flex;align-items:center;justify-content:center}
.socials span::before{content:"";width:12px;height:12px;border-radius:3px;background:var(--orange)}
.phone{left:720px;top:24px;display:flex;align-items:center;gap:12px;font:500 19px Roboto,sans-serif}
.phone-ic{width:42px;height:42px;border-radius:50%;background:var(--orange);display:flex;align-items:center;justify-content:center}
.nav{left:300px;top:88px;width:900px;height:47px;background:var(--orange);clip-path:polygon(0 0,100% 0,100% 100%,14px 100%)}
.nav ul{list-style:none;display:flex;align-items:center;height:47px;padding-left:53px;color:#fff;font:400 14px Roboto,sans-serif}
.nav li.sep{margin:0 48px}

/* hero */
.hero{left:0;top:135px;width:1200px;height:620px;background:
  radial-gradient(ellipse 120px 90px at 700px 420px,rgba(255,190,90,.85),transparent 70%),
  radial-gradient(ellipse 220px 300px at 640px 120px,#8d8d90 0,#45464a 45%,transparent 75%),
  radial-gradient(ellipse 520px 260px at 640px 540px,#c98a3c 0,#7a5426 40%,transparent 80%),
  linear-gradient(120deg,#1a1714 0,#3b2c1c 45%,#5a4a38 70%,#1c1a18 100%)}
.hero-shade{left:0;top:135px;width:700px;height:620px;background:linear-gradient(90deg,rgba(0,0,0,.45),transparent)}
.hero-kicker{left:101px;top:314px;font:700 21px Montserrat,sans-serif;color:#fff}
.hero-title{left:101px;top:354px;font:800 70px/1 Montserrat,sans-serif;color:#fff;text-transform:uppercase}
.hero-dots{left:1136px;top:395px;display:flex;flex-direction:column;gap:11px}
.hero-dots i{width:9px;height:9px;border-radius:50%;background:#fff}
.hero-dots i.on{background:transparent;border:2px solid #fff}

/* quote */
.quote{left:0;top:755px;width:1200px;height:620px;background:var(--cream);clip-path:polygon(0 0,100% 0,100% 578px,0 620px)}
.field{position:absolute;background:#fff;border:1px solid var(--line);border-radius:2px;font:400 12px Roboto,sans-serif;color:#333;padding:0 0 0 48px;display:flex;align-items:center}
.field::before{content:"";position:absolute;left:26px;width:9px;height:9px;background:#222;border-radius:2px}
.field.area{align-items:flex-start;padding-top:20px}
.field.area::before{top:21px}

/* services */
.card{position:absolute;top:1522px;width:236px;height:333px;background:#fff;border-radius:8px;box-shadow:0 2px 10px rgba(0,0,0,.16);text-align:center}
.card .photo{left:5px;top:5px;width:226px;height:161px}
.card h3{position:absolute;top:180px;width:100%;font:500 15px Roboto,sans-serif}
.card p{position:absolute;top:220px;left:18px;right:18px;font:400 10.5px/1.65 Roboto,sans-serif;color:var(--muted)}
.card .btn{top:290px;left:65px;width:106px;height:27px;font-size:10px;gap:6px}
.ph-print{background:radial-gradient(ellipse 70px 40px at 90px 95px,#6ea0e6,transparent 80%),radial-gradient(ellipse 60px 70px at 130px 40px,#d6242c,transparent 80%),linear-gradient(180deg,#3a3a3c,#1f1f21 70%,#5a5a5c)}
.ph-scan{background:radial-gradient(ellipse 50px 30px at 150px 120px,#5a4cf0,transparent 80%),radial-gradient(ellipse 80px 50px at 80px 40px,#f1f1f1,transparent 80%),linear-gradient(180deg,#d9d9d9,#2a2a30 55%,#1c1c22)}
.ph-cad{background:radial-gradient(ellipse 60px 40px at 60px 70px,#5f8aa0,transparent 80%),radial-gradient(ellipse 50px 80px at 180px 100px,#8c5e40,transparent 80%),linear-gradient(180deg,#6f7f6c,#2e3a3e 60%,#222)}
.ph-draft{background:radial-gradient(ellipse 50px 40px at 200px 30px,#f2c91c,transparent 80%),radial-gradient(ellipse 100px 60px at 110px 110px,#f4f4f2,transparent 85%),linear-gradient(180deg,#c9c6c0,#a9a59d)}
.arrow{position:absolute;width:14px;height:14px;border-right:1.5px solid #888;border-bottom:1.5px solid #888}
.arrow.l{transform:rotate(135deg)}
.arrow.r{transform:rotate(-45deg)}

/* tech */
.tech-l{left:0;top:1990px;width:600px;height:436px;background:radial-gradient(ellipse 300px 200px at 150px 120px,rgba(255,170,90,.35),transparent 80%),linear-gradient(135deg,#ff8a24,#f3700d 60%,#e4660a);clip-path:polygon(0 0,600px 58px,600px 378px,0 436px)}
.tech-r{left:600px;top:1990px;width:600px;height:436px;background:radial-gradient(ellipse 300px 200px at 420px 120px,rgba(90,90,90,.45),transparent 80%),linear-gradient(135deg,#2a2a2a,#161616);clip-path:polygon(0 58px,600px 0,600px 436px,0 378px)}
.tech-ic{width:84px;height:84px;border-radius:50%;background:#fff;display:flex;align-items:center;justify-content:center}
.tech-name{font:500 21px Roboto,sans-serif;color:#fff}
.tech-text{width:420px;font:400 13.5px/1.85 Roboto,sans-serif;color:#fff}

/* products */
.prod{position:absolute;top:2595px;width:220px;text-align:center}
.prod .photo{position:relative;width:220px;height:225px;background:#efefef}
.prod h4{margin-top:28px;font:500 14.5px Roboto,sans-serif}
.prod a{display:block;margin-top:12px;font:500 14px Roboto,sans-serif;color:var(--orange);text-decoration:none}
.ph-nozzle{background:radial-gradient(ellipse 28px 60px at 110px 115px,#9a9a9a,#6f6f6f 55%,transparent 80%) ,#efefef !important}
.ph-printer{background:radial-gradient(ellipse 62px 55px at 110px 110px,#ffffff,#d8d8d8 60%,transparent 85%),radial-gradient(ellipse 40px 14px at 110px 80px,#444,transparent 80%),#efefef !important}
.ph-mould{background:radial-gradient(ellipse 85px 42px at 110px 118px,#b9bcc0,#7d8185 60%,transparent 85%),#efefef !important}
.ph-bush{background:radial-gradient(ellipse 42px 38px at 85px 125px,#c8c8c8,#8a8a8a 65%,transparent 85%),radial-gradient(ellipse 38px 34px at 145px 95px,#d6d6d6,#909090 65%,transparent 85%),#efefef !important}

/* about */
.about-photo{left:0;top:2988px;width:600px;height:512px;background:
  radial-gradient(ellipse 200px 140px at 420px 130px,#2f5d8c,transparent 80%),
  radial-gradient(ellipse 260px 120px at 300px 400px,#b9bec4,#7e858c 55%,transparent 85%),
  radial-gradient(ellipse 90px 70px at 220px 180px,#4a4a4a,transparent 80%),
  linear-gradient(160deg,#3e4a57,#5b636b 50%,#2e3238 100%)}
.about-bg{left:600px;top:2988px;width:600px;height:512px;background:var(--cream)}
.about-title{left:676px;top:3054px;font:700 34px Montserrat,sans-serif;text-transform:uppercase}
.about-title::after{content:"";display:block;width:40px;height:2px;background:var(--orange);margin-top:10px}
.about-text{left:676px;top:3124px;width:412px;font:400 13.6px/1.95 Roboto,sans-serif;color:#777;text-align:justify}

/* testimonials */
.tcard{position:absolute;top:3680px;width:418px;height:184px;background:#fff;border-radius:6px;box-shadow:0 2px 12px rgba(0,0,0,.13)}
.tcard::after{content:"";position:absolute;left:55px;bottom:-10px;border:10px solid transparent;border-top-color:#fff;border-bottom:0}
.tcard .q{position:absolute;font:700 54px/1 Georgia,serif;color:var(--orange)}
.tcard p{position:absolute;left:67px;top:46px;width:326px;font:400 13.5px/1.9 Roboto,sans-serif;color:#888;text-align:justify}
.person{position:absolute;top:3906px;display:flex;align-items:center;gap:22px}
.avatar{width:70px;height:70px;border-radius:50%;background:radial-gradient(circle at 50% 40%,#c9a58a 0,#9a7a62 35%,#3a4a5c 75%);border:3px solid #fde7d6}
.person b{display:block;font:500 16px Roboto,sans-serif}
.person span{display:block;margin-top:6px;font:400 13px Roboto,sans-serif;color:#777}
.circ{position:absolute;width:32px;height:32px;border-radius:50%;display:flex;align-items:center;justify-content:center}

/* footer */
.footer{left:0;top:4053px;width:1200px;height:242px;background:var(--charcoal)}
.foot-brand{left:110px;top:4140px;width:200px;font:800 23px/1.25 Montserrat,sans-serif;color:var(--orange);text-transform:uppercase}
.foot-contact{left:374px;top:4140px;display:flex;align-items:center;color:#fff;font:400 14px Roboto,sans-serif}
.foot-contact .sep{margin:0 28px}
.foot-line{left:374px;top:4176px;width:716px;height:1px;background:#555}
.foot-nav{left:374px;top:4203px;display:flex;color:#fff;font:700 15px Roboto,sans-serif}
.foot-nav .sep{margin:0 38px;font-weight:400}
.copy{left:0;top:4295px;width:1200px;height:50px;background:var(--orange);color:#fff;font:400 13px Roboto,sans-serif;display:flex;align-items:center;justify-content:space-between;padding:0 112px 0 110px}
</style>
</head>
<body>

<!-- Header -->
<div class="abs brand-block"></div>
<div class="abs brand-name">Korvath<br>Draft &amp; Design</div>
<div class="abs socials"><span></span><span></span><span></span></div>
<div class="abs phone">
  <div class="phone-ic"><svg width="20" height="20" viewBox="0 0 24 24"><path fill="#fff" d="M6.6 10.8a15.1 15.1 0 0 0 6.6 6.6l2.2-2.2a1 1 0 0 1 1-.25 11.4 11.4 0 0 0 3.6.57 1 1 0 0 1 1 1V20a1 1 0 0 1-1 1A17 17 0 0 1 3 4a1 1 0 0 1 1-1h3.5a1 1 0 0 1 1 1c0 1.25.2 2.45.57 3.57a1 1 0 0 1-.25 1z"/></svg></div>
  +1 555 014 2287
</div>
<div class="btn" style="left:946px;top:24px;width:142px;height:42px">Get a quote <span class="dot"></span></div>
<nav class="abs nav"><ul><li>HOME</li><li class="sep">/</li><li>ABOUT US</li><li class="sep">/</li><li>SERVICES</li><li class="sep">/</li><li>TIMONIALS</li><li class="sep">/</li><li>CONTACT US</li></ul></nav>

<!-- Hero -->
<div class="photo hero" role="img" aria-label="CNC milling head cutting metal with sparks"></div>
<div class="abs hero-shade"></div>
<div class="abs hero-kicker">WELCOME TO</div>
<h1 class="abs hero-title">Korvath Draft &amp;<br>Design</h1>
<div class="btn" style="left:101px;top:526px;width:144px;height:44px">Get started <span class="dot"></span></div>
<div class="abs hero-dots"><i></i><i></i><i class="on"></i><i></i><i></i></div>

<!-- Get a quote -->
<section class="abs quote"></section>
<h2 class="sec-title" style="top:815px">Get a quote</h2>
<div class="field" style="left:160px;top:903px;width:433px;height:43px">First Name</div>
<div class="field" style="left:607px;top:903px;width:433px;height:43px">Last Name</div>
<div class="field" style="left:160px;top:966px;width:433px;height:43px">Email</div>
<div class="field" style="left:607px;top:966px;width:433px;height:43px">Phone</div>
<div class="field area" style="left:160px;top:1028px;width:880px;height:147px">Comments</div>
<div class="btn" style="left:512px;top:1214px;width:156px;height:45px;font-size:14px">Submit now
  <svg width="13" height="13" viewBox="0 0 24 24"><path fill="#fff" d="M2 11 22 2l-9 20-2-8z"/></svg></div>

<!-- Services -->
<h2 class="sec-title" style="top:1445px">Our services</h2>
<div class="arrow l" style="left:55px;top:1688px"></div>
<div class="arrow r" style="left:1128px;top:1688px"></div>
<div class="card" style="left:109px"><div class="photo ph-print" role="img" aria-label="3D printer producing a blue 3D model"></div><h3>3d Printing</h3><p>Lorem ipsum dolor sit amet, consectetur adipiscing elit, sed do eiusmod tempor incididunt ut labore</p><div class="btn">Learn more <span class="dot"></span></div></div>
<div class="card" style="left:358px"><div class="photo ph-scan" role="img" aria-label="3D scanner scanning an object under blue light"></div><h3>3d Scanning</h3><p>Lorem ipsum dolor sit amet, consectetur adipiscing elit, sed do eiusmod tempor incididunt ut labore</p><div class="btn">Learn more <span class="dot"></span></div></div>
<div class="card" style="left:607px"><div class="photo ph-cad" role="img" aria-label="Engineers working on CAD models at computer screens"></div><h3>3d Cad Design</h3><p>Lorem ipsum dolor sit amet, consectetur adipiscing elit, sed do eiusmod tempor incididunt ut labore</p><div class="btn">Learn more <span class="dot"></span></div></div>
<div class="card" style="left:856px"><div class="photo ph-draft" role="img" aria-label="Engineers reviewing drafted plans with a hard hat"></div><h3>Drafting Services</h3><p>Lorem ipsum dolor sit amet, consectetur adipiscing elit, sed do eiusmod tempor incididunt ut labore</p><div class="btn">Learn more <span class="dot"></span></div></div>

<!-- 3D printing technologies -->
<h2 class="sec-title" style="top:1935px">Our 3d printing technologies</h2>
<div class="photo tech-l" role="img" aria-label="Factory floor with orange tint"></div>
<div class="photo tech-r" role="img" aria-label="Workshop machinery in dark tones"></div>
<div class="abs" style="left:110px;top:2070px;display:flex;align-items:center;gap:32px">
  <div class="tech-ic"><svg width="44" height="44" viewBox="0 0 44 44" fill="none" stroke="#fc7a12" stroke-width="2"><rect x="8" y="5" width="26" height="34" rx="2"/><path d="M13 14h16M13 20h16M13 26h10"/><circle cx="32" cy="32" r="6"/></svg></div>
  <div class="tech-name">SLA</div>
</div>
<p class="abs tech-text" style="left:112px;top:2172px">Lorem ipsum dolor sit amet, consectetur adipiscing elit, sed do eiusmod tempor incididunt ut labore et dolore magna aliqua. Ut ad minim veniam, quis nostrud exercitation ullamco laboris nisi ut aliquip ex ea commodo consequat.</p>
<div class="btn ghost" style="left:112px;top:2305px;width:150px;height:42px">Learn more <span class="dot"></span></div>
<div class="abs" style="left:677px;top:2070px;display:flex;align-items:center;gap:32px">
  <div class="tech-ic"><svg width="44" height="44" viewBox="0 0 44 44" fill="none" stroke="#fc7a12" stroke-width="2"><path d="M8 6h28M22 6v10M16 16h12l-3 8h-6z"/><path d="M22 24v4"/><rect x="10" y="32" width="24" height="6"/></svg></div>
  <div class="tech-name">FDM</div>
</div>
<p class="abs tech-text" style="left:678px;top:2172px">Lorem ipsum dolor sit amet, consectetur adipiscing elit, sed do eiusmod tempor incididunt ut labore et dolore magna aliqua. Ut ad minim veniam, quis nostrud exercitation ullamco laboris nisi ut aliquip ex ea commodo consequat.</p>
<div class="btn ghost" style="left:678px;top:2305px;width:150px;height:42px">Learn more <span class="dot"></span></div>

<!-- Products -->
<h2 class="sec-title" style="top:2498px">My custom automotive parts</h2>
<div class="arrow l" style="left:66px;top:2708px"></div>
<div class="arrow r" style="left:1120px;top:2708px"></div>
<div class="prod" style="left:115px"><div class="photo ph-nozzle" role="img" aria-label="Threaded metal nozzle part"></div><h4>Lorem ipsum dolor sit amet</h4><a>Shop Now &nbsp;🛒</a></div>
<div class="prod" style="left:366px"><div class="photo ph-printer" role="img" aria-label="Desktop printer unit"></div><h4>Lorem ipsum dolor sit amet</h4><a>Shop Now &nbsp;🛒</a></div>
<div class="prod" style="left:617px"><div class="photo ph-mould" role="img" aria-label="Machined metal mould block"></div><h4>Lorem ipsum dolor sit amet</h4><a>Shop Now &nbsp;🛒</a></div>
<div class="prod" style="left:868px"><div class="photo ph-bush" role="img" aria-label="Machined aluminium bushings"></div><h4>Lorem ipsum dolor sit amet</h4><a>Shop Now &nbsp;🛒</a></div>

<!-- About -->
<div class="photo about-photo" role="img" aria-label="Worker measuring steel profiles with a caliper"></div>
<div class="abs about-bg"></div>
<h2 class="abs about-title">About us</h2>
<p class="abs about-text">Sed perspiciatis unde omnis iste natus error sit voluptatem accusantium doloremque laudantium, totam rem aperiam, eaque ipsa quae ab illo inventore veritatis et quasi architecto beatae vitae dicta sunt explicabo. Nemo enim ipsam voluptatem quia voluptas sit aspernatur aut odit aut fugit, sed quia consequuntur magni dolores eos qui ratione voluptatem sequi nesciunt. Neque porro quisquam est, qui dolorem ipsum quia dolor sit amet, consectetur, adipisci velit, sed quia non numquam eius modi tempora incidunt</p>
<div class="btn" style="left:676px;top:3385px;width:144px;height:42px">Learn more <span class="dot"></span></div>

<!-- Testimonials -->
<h2 class="sec-title" style="top:3580px">My custom automotive parts</h2>
<div class="circ" style="left:79px;top:3756px;background:#fde7d6"><svg width="10" height="12" viewBox="0 0 10 12"><path d="M8 1 2 6l6 5" fill="none" stroke="#fc7a12" stroke-width="2"/></svg></div>
<div class="circ" style="left:1089px;top:3756px;background:var(--orange)"><svg width="10" height="12" viewBox="0 0 10 12"><path d="m2 1 6 5-6 5" fill="none" stroke="#fff" stroke-width="2"/></svg></div>
<div class="tcard" style="left:147px"><span class="q" style="left:14px;top:28px">“</span><p>Sed ut perspiciatis unde omnis iste sit voluptatem accusantium doloremque laudantium, totam aperiam, eaque ipsa quae ab illo inventore veritatis et quasi beatae sunt explicabo.</p><span class="q" style="left:275px;top:112px">”</span></div>
<div class="tcard" style="left:635px"><span class="q" style="left:14px;top:28px">“</span><p>Sed ut perspiciatis unde omnis iste sit voluptatem accusantium doloremque laudantium, totam aperiam, eaque ipsa quae ab illo inventore veritatis et quasi beatae sunt explicabo.</p><span class="q" style="left:275px;top:112px">”</span></div>
<div class="person" style="left:150px"><div class="avatar" role="img" aria-label="Customer portrait"></div><div><b>John Doe</b><span>Lorem ipsum dolor</span></div></div>
<div class="person" style="left:638px"><div class="avatar" role="img" aria-label="Customer portrait"></div><div><b>John Doe</b><span>Lorem ipsum dolor</span></div></div>

<!-- Footer -->
<footer class="abs footer"></footer>
<div class="abs foot-brand">Korvath<br>Draft &amp; Design</div>
<div class="abs foot-contact">
  <svg width="16" height="13" viewBox="0 0 16 13" style="margin-right:16px"><rect x="1" y="1" width="14" height="11" fill="none" stroke="#fff" stroke-width="1.5"/><path d="m1 1 7 6 7-6" fill="none" stroke="#fff" stroke-width="1.5"/></svg>info@korvathdraft.com
  <span class="sep">|</span>
  <svg width="14" height="14" viewBox="0 0 24 24" style="margin-right:16px"><path fill="#fff" d="M6.6 10.8a15.1 15.1 0 0 0 6.6 6.6l2.2-2.2a1 1 0 0 1 1-.25 11.4 11.4 0 0 0 3.6.57 1 1 0 0 1 1 1V20a1 1 0 0 1-1 1A17 17 0 0 1 3 4a1 1 0 0 1 1-1h3.5a1 1 0 0 1 1 1c0 1.25.2 2.45.57 3.57a1 1 0 0 1-.25 1z"/></svg>+1 555 014 2287
  <span class="sep">|</span>
  <svg width="12" height="16" viewBox="0 0 12 16" style="margin-right:18px"><path fill="#fff" d="M6 0a6 6 0 0 1 6 6c0 4.5-6 10-6 10S0 10.5 0 6a6 6 0 0 1 6-6zm0 3.5A2.5 2.5 0 1 0 6 8.5 2.5 2.5 0 0 0 6 3.5z"/></svg>156 , Lorem Ipsum Dolor , USA
</div>
<div class="abs foot-line"></div>
<div class="abs foot-nav"><span>HOME</span><span class="sep">/</span><span>ABOUT US</span><span class="sep">/</span><span>SERVICES</span><span class="sep">/</span><span>TIMONIALS</span><span class="sep">/</span><span>CONTACT US</span></div>
<div class="abs copy"><span>© 2023 Korvath Draft &amp; Design. All Rights Reserved</span><span>Terms &amp; Conditions / Privacy Policy</span></div>

</body>
</html>
```